Valderons Business Card

Business card for philanthropic organization

Industry/Entity Type

Business

Contact Information for Business Card

Need a very ELEGANT, sober, embossed, formal business card... it should transmit CREDIBILITY. Not looking for a "fun card". would like white, grays or black designs.

Font styles to use
Script

Requirements
Must have
• Embossed look

```html
<!DOCTYPE html>
<html lang="en">
<head>
<meta charset="UTF-8">
<title>Valderons Business Card</title>
<link rel="stylesheet" href="https://fonts.googleapis.com/css2?family=Italianno&family=Open+Sans:wght@400;600&display=swap">
<style>
  :root {
    --backdrop: #e4e2df;
    --card-top: #ffffff;
    --card-bottom: #ececec;
    --ink: #1b1b1b;
    --ink-soft: #3a3a3a;
    --mark: #6e6e6e;
    --edge: #d6d6d6;
  }
  * { margin: 0; padding: 0; box-sizing: border-box; }
  html, body {
    width: 1200px;
    height: 1023px;
    overflow: hidden;
    background: var(--backdrop);
  }
  .canvas {
    width: 1200px;
    height: 1023px;
    display: flex;
    align-items: center;
    justify-content: center;
  }
  .card {
    position: relative;
    width: 900px;
    height: 514px;
    background: linear-gradient(160deg, var(--card-top) 0%, #f7f7f7 55%, var(--card-bottom) 100%);
    border: 1px solid var(--edge);
    border-radius: 4px;
    box-shadow: 0 2px 0 #dcdcdc, 0 4px 0 #d2d2d2, 0 18px 40px rgba(0,0,0,0.18);
  }
  .brand {
    position: absolute;
    left: 70px;
    top: 330px;
    display: flex;
    align-items: center;
    gap: 14px;
  }
  .brand-dot {
    width: 22px;
    height: 22px;
    border-radius: 50%;
    background: var(--mark);
  }
  .brand-name {
    font-family: "Open Sans", sans-serif;
    font-weight: 600;
    font-size: 30px;
    letter-spacing: 1px;
    color: var(--mark);
  }
  .contact {
    position: absolute;
    left: 470px;
    top: 120px;
    color: var(--ink);
  }
  .person-name {
    font-family: "Italianno", cursive;
    font-size: 78px;
    line-height: 1;
    color: var(--ink);
    text-shadow: 0 1px 0 #fff, 0 -1px 0 rgba(0,0,0,0.12);
  }
  .person-role {
    font-family: "Italianno", cursive;
    font-size: 30px;
    line-height: 1;
    margin: 2px 0 22px 60px;
    color: var(--ink-soft);
  }
  .details {
    list-style: none;
    font-family: "Open Sans", sans-serif;
    font-size: 19px;
    line-height: 1.75;
    color: var(--ink);
    text-shadow: 0 1px 0 #fff;
  }
  .details .label { font-weight: 400; }
</style>
</head>
<body>
  <main class="canvas">
    <section class="card">
      <div class="brand">
        <span class="brand-dot"></span>
        <span class="brand-name">Valderons</span>
      </div>
      <div class="contact">
        <h1 class="person-name">Martin Alvear</h1>
        <p class="person-role">Director</p>
        <ul class="details">
          <li><span class="label">C:</span> +(507)-6240-3187</li>
          <li><span class="label">E:</span> m.alvear@valderons.org</li>
          <li><span class="label">A:</span> P.O. Box 0816-02715</li>
          <li>Panama, Republic of Panama</li>
        </ul>
      </div>
    </section>
  </main>
</body>
</html>
```